Web Design Project

We are an online tax Continuing education provider. We provide online courses for tax preparers. We want the front end page to be user friendly and for the buyer to know exactly what they are looking at. We want a front end page to look smiliar www.larkvalefiling.com. It should have a similar feel to this one.
Our website address will be www.7782QX.com
We currently have another website that is www.LedgrUMs.com but we do not want it to look like this. We want a different look but same information.
We have a logo already which is attached. We don't have specific colors in mind for the front page but don't want it to be too busy looking. It should stand out but not too simple either.
Target Market(s)
Tax Preparers. More serious and professional but these folks are usually not tech savy. Simple, easy to use, and functional is key.
Industry/Entity Type
Education
Requirements
Must have
- Use standard HTML & CSS. NO other coding is needed.
We are looking for 5-7 pages including Home page, log in, FAQ.
Please look at our current website www.LedgrUMs.com and also www.larkvalefiling.com

```html
<!DOCTYPE html>
<html lang="en">
<head>
<meta charset="utf-8">
<title>7782QX – Continuing Education</title>
<link href="https://fonts.googleapis.com/css2?family=Open+Sans:wght@400;600&family=Roboto+Condensed:wght@400;700&display=swap" rel="stylesheet">
<style>
:root{
  --teal:#1f6a80;
  --teal-dark:#1d4f66;
  --orange:#f7bb4f;
  --orange-deep:#f5a93a;
  --orange-text:#f0a233;
  --grey-band:#9a9a9c;
  --grey-page:#e9e9e9;
  --text:#6b6b6b;
  --white:#ffffff;
  --footer:#a3a3a5;
}
*{margin:0;padding:0;box-sizing:border-box}
html,body{width:991px;height:1200px;overflow:hidden}
body{position:relative;background:var(--grey-page);font-family:"Open Sans",sans-serif;color:var(--text)}
.abs{position:absolute}
.header{left:0;top:0;width:991px;height:118px;background:var(--white);z-index:2}
.brand{left:128px;top:70px;display:flex;align-items:center;gap:8px;font-size:24px;font-weight:600;color:var(--teal-dark)}
.brand-dot{width:16px;height:16px;border-radius:50%;background:var(--teal)}
.nav{left:457px;top:80px;display:flex;font-size:12px;color:#222}
.nav a{color:inherit;text-decoration:none;margin-right:54px}
.signin{left:791px;top:77px;width:76px;height:25px;border-radius:4px;background:#d7dadd;border:1px solid #c7cacd;font-size:12px;color:var(--teal);display:flex;align-items:center;justify-content:center;gap:7px}
.hero{left:0;top:118px;width:991px;height:260px;background:linear-gradient(#f1f1f1,#cfcfd0)}
.hero-band{left:0;top:378px;width:991px;height:48px;background:var(--grey-band)}
.tagline{left:124px;top:164px;width:285px;font-family:"Roboto Condensed",sans-serif;font-weight:400;font-size:18.5px;line-height:37.5px;color:var(--teal);letter-spacing:-.3px;white-space:nowrap}
.tagline b{font-weight:700}
.dots{left:124px;top:336px;display:flex;gap:6px}
.dots span{width:10px;height:10px;border-radius:50%;background:#bbb;box-shadow:inset 0 1px 2px #777}
.dots span.on{background:#fff;box-shadow:none}
.photo-frame{left:419px;top:160px;width:448px;height:243px;background:#fff;box-shadow:0 3px 6px rgba(0,0,0,.35);padding:6px 5px}
.photo{width:100%;height:100%;background:linear-gradient(110deg,#e3a049 0%,#c98a46 40%,#8a8682 65%,#d7a35f 100%)}
.features{left:124px;top:442px;display:flex;gap:8px}
.feature{position:relative;width:242px;height:112px;background:linear-gradient(var(--orange),var(--orange-deep));color:var(--white);padding:14px 14px 0}
.feature h3{font-weight:400;font-size:13.5px;line-height:23px;width:150px}
.feature p{position:absolute;left:14px;bottom:10px;font-size:9.5px;line-height:16px;color:#5a3e10;white-space:nowrap}
.feature .icon{position:absolute;right:18px;top:16px}
.contact-band{left:0;top:574px;width:991px;height:62px;background:linear-gradient(#d4d4d5,#e6e6e6)}
.contact-title{left:124px;top:594px;font-size:14px;font-weight:400;color:var(--teal)}
.intro{left:124px;top:654px;font-size:9.5px;line-height:30px}
.email{left:124px;top:718px;width:213px;height:29px;background:#fff;border-radius:2px;font-size:9.5px;color:var(--teal);display:flex;align-items:center;padding-left:8px;gap:10px;white-space:nowrap}
.card{top:771px;width:213px;height:253px;background:#f4f4f4;border:1px solid #dcdcdc;padding:18px 15px}
.card h4{font-weight:400;font-size:13.5px;color:var(--orange-text);margin-bottom:24px}
.card::after{content:"";position:absolute;left:102px;bottom:-6px;width:10px;height:10px;background:#f4f4f4;border-right:1px solid #dcdcdc;border-bottom:1px solid #dcdcdc;transform:rotate(45deg)}
.field{width:181px;background:#fff;border:1px solid #d5d5d5;border-bottom:3px solid #e4e4e4;font-family:Arial,sans-serif;font-size:11px;color:#555;padding:8px 13px}
.btn{position:absolute;left:113px;top:207px;width:88px;height:27px;border-radius:4px;background:linear-gradient(#fbc863,var(--orange-deep));color:#fff;font-size:11px;display:flex;align-items:center;justify-content:center}
.call p{font-size:9px;line-height:19px;white-space:nowrap}
.call .teal{color:var(--teal)}
.big{font-size:14.5px}
.mail p{font-size:11px;color:var(--teal);line-height:28px;white-space:nowrap}
.footer{left:0;top:1157px;width:991px;height:43px;background:var(--footer);color:#fff;font-size:9.5px}
.footer .copy{left:124px;top:16px}
.footer .links{left:412px;top:15px;color:#e2eef2}
.footer .social{left:731px;top:12px;display:flex;align-items:center;gap:7px}
.footer .social i{width:17px;height:17px;border-radius:50%;background:#d6d6d6;display:block}
</style>
</head>
<body>
<header class="header abs">
  <div class="brand abs"><span class="brand-dot"></span>7782QX</div>
  <nav class="nav abs"><a href="#">Home</a><a href="#">Courses</a><a href="#">FAQ</a><a href="#">Contact</a></nav>
  <div class="signin abs">
    <svg width="8" height="10" viewBox="0 0 8 10"><circle cx="4" cy="2.5" r="2.3" fill="#1f6a80"/><path d="M0 10a4 4 0 0 1 8 0z" fill="#1f6a80"/></svg>Sign In
  </div>
</header>

<section class="hero abs"></section>
<div class="hero-band abs"></div>
<h1 class="tagline abs"><b>EASY-TO-UNDERSTAND,</b><br><b>AFFORDABLE</b> CONTINUING EDUCATION<br>AT YOUR FINGER TIPS</h1>
<div class="dots abs"><span></span><span></span><span></span><span class="on"></span></div>
<div class="photo-frame abs"><div class="photo" role="img" aria-label="Photo of a student studying on a laptop in a lecture hall"></div></div>

<section class="features abs">
  <div class="feature">
    <h3>IRS APPROVED PROVIDER</h3>
    <svg class="icon" width="58" height="50"><circle cx="29" cy="25" r="23" fill="none" stroke="#fff" stroke-width="3"/></svg>
    <p>Click here to see our<br>approved provider link at IRS website</p>
  </div>
  <div class="feature">
    <h3>CERTIFICATE OF COMPLETION</h3>
    <svg class="icon" width="46" height="38"><rect x="1" y="1" width="44" height="36" fill="#f6f6f6" stroke="#8a8a8a"/><rect x="5" y="5" width="36" height="28" fill="none" stroke="#b5b5b5"/><line x1="10" y1="13" x2="30" y2="13" stroke="#888"/><line x1="10" y1="18" x2="26" y2="18" stroke="#888"/><circle cx="34" cy="25" r="4" fill="#f2c23b"/></svg>
    <p>IMPORTANT! All federal tax return&nbsp; preparers<br>must have a current year PTIN.</p>
  </div>
  <div class="feature">
    <h3>PROFESSIONAL</h3>
    <svg class="icon" width="54" height="52"><rect x="4" y="10" width="40" height="38" rx="3" fill="#e8e0c8" stroke="#777" transform="rotate(-10 24 29)"/><line x1="16" y1="42" x2="38" y2="8" stroke="#e19a1e" stroke-width="5"/></svg>
    <p>Complete your continuing education<br>requirements now so you can concentrate<br>on servicing your tax clients.</p>
  </div>
</section>

<div class="contact-band abs"></div>
<h2 class="contact-title abs">Contact Us</h2>
<p class="intro abs">For your convenience, our online continuing education courses are available 24 hours per day, 7 days per week.<br>Please contact us for any technical, billing or support needs via the following :</p>
<div class="email abs">
  <svg width="14" height="9"><rect width="14" height="9" fill="#1f6a80"/><path d="M0 0l7 5 7-5" fill="none" stroke="#fff"/></svg>
  Email address: support@ledgrums.com
</div>

<div class="card abs" style="left:124px">
  <h4>Support :</h4>
  <div class="field" style="height:30px;padding-top:7px">Email Address*</div>
  <div class="field" style="height:91px;margin-top:14px">Message*</div>
  <div class="btn">Submit</div>
</div>
<div class="card call abs" style="left:374px">
  <h4>Call Us :</h4>
  <p style="margin-top:-4px">You can also call us at the number below :</p>
  <p class="teal" style="margin-top:8px">Toll Free number : <span class="big">800-555-0142</span></p>
  <p class="teal" style="margin-top:14px">Hours of operation : <span style="font-size:11px">9:30am - 5:00pm</span></p>
  <p>Central Time</p>
  <p>Monday thru Friday</p>
</div>
<div class="card mail abs" style="left:624px">
  <h4 style="margin-bottom:14px">Mailing Address :</h4>
  <p>QUILLMARK EDUCATION, LLC</p>
  <p>2210 Harlow St.</p>
  <p>Marlow, TX 77590</p>
</div>

<footer class="footer abs">
  <span class="copy abs">Copyright © 2012. All Rights Reserved</span>
  <span class="links abs">Terms &amp; Condition &nbsp; | &nbsp; Privacy Policy</span>
  <div class="social abs"><span style="margin-right:14px">Social Media</span><i></i><i></i><i></i></div>
</footer>
</body>
</html>
```